Health and Fitness Club requires a stunning and simple website

We are a health and fitness club based in Dubai, when we launch we will be the biggest club in the country, we will also have the 2 largest activity rooms in the country, we are setting a new standard in the industry by offering one thing, our attitude.

Our attitude means the following:
unlike other clubs we have no hidden charges or fees
our members can join daily, monthly, 6 months or annually
our service and facility are comparable to 5* hotel gyms
our equipment is second to none
our space is the biggest in the country
we do not force our members to use our in-house personal trainers - you can bring your own and we will not charge them entry!
we will have a cutting edge brawnmesh box in our gym with classes by the best trainers in the country
we will be providing free-lance personal trainers a platform to engage customers, grow their business and even use our activity rooms for classes

Basically we will be a gym like no other, simply because we are gym people and we hate the restrictive practices and hidden charges by other gyms, so we are making our own gym which focuses on quality and service.

All of this has to be communicated in the style of the website, the colors of the website we want to be limited to the logo colors as this will be the same theme running throughout the gym.

The landing page of the website HAS to incorporate elements from our social media presences, this basically is the usual, chirplo, snapvault, kinwall. We can have these as a sidebar, the centre of the page should display the latest article from our blog (also on the website) Also we need to have a calendar for activities and classes on the front page. The menu should have links to the following:
Latest News
About us
Team
Gallery
Membership
Classes
Member Log In
Contact Us
Location

The style of the website has to be similar to the logo, particularly in terms of the fonts used.

```html
<!DOCTYPE html>
<html lang="en">
<head>
<meta charset="utf-8">
<title>Vantage Fitness</title>
<link href="https://fonts.googleapis.com/css2?family=Bebas+Neue&family=Open+Sans:wght@300;400;600;700&display=swap" rel="stylesheet">
<style>
:root{
  --red:#c4121c;
  --red-dark:#3a0508;
  --page:#f1f1f1;
  --ink:#4a4a4a;
  --muted:#8a8a8a;
  --line:#dedede;
  --white:#ffffff;
  --cal-head:#3b3b3b;
}
*{box-sizing:border-box;margin:0;padding:0}
html,body{width:942px;height:1200px;overflow:hidden}
body{position:relative;background:var(--page);font-family:"Open Sans",sans-serif;color:var(--ink)}
.display{font-family:"Bebas Neue",sans-serif;font-weight:400;letter-spacing:.2px}

.brand{position:absolute;left:102px;top:30px;display:flex;align-items:center;gap:8px}
.brand-dot{width:38px;height:38px;border-radius:50%;background:var(--red)}
.brand-name{font-family:"Bebas Neue",sans-serif;font-size:28px;color:var(--red);line-height:1}

.search{position:absolute;left:672px;top:83px;width:164px;height:17px;background:#e2e2e2;font-size:9px;color:#777;padding:2px 6px;line-height:13px}

.main-nav{position:absolute;left:102px;top:108px;width:738px;height:50px;background:var(--red);display:flex;align-items:center;justify-content:space-between;padding:0 15px}
.main-nav a{font-family:"Bebas Neue",sans-serif;font-size:21px;color:var(--white);text-decoration:none}

.hero{position:absolute;left:102px;top:168px;width:738px;height:292px;background:linear-gradient(90deg,var(--red-dark) 0%,#4a0a0d 45%,#7a1a18 70%,#5a1210 100%);overflow:hidden}
.hero-photo{position:absolute;right:0;top:0;width:420px;height:292px;background:linear-gradient(90deg,rgba(80,15,12,0) 0%,#8a4a35 35%,#b07050 60%,#6b2a1e 85%,#2a0a08 100%)}
.hero-title{position:absolute;left:40px;top:92px;color:var(--white);line-height:.95}
.hero-title .l1{font-size:46px;display:block}
.hero-title .l2{font-size:33px;display:block}
.hero-arrows{position:absolute;left:42px;top:230px}

.social{position:absolute;right:0;top:382px;width:38px}
.social a{display:flex;align-items:center;justify-content:center;height:36px;margin-bottom:4px;background:var(--red);color:var(--white);font-size:7px;font-weight:600;text-decoration:none;border-radius:3px 0 0 3px}

.welcome h1{position:absolute;left:102px;top:486px;width:738px;text-align:center;font-size:22px;color:var(--red)}
.welcome p{position:absolute;left:102px;top:530px;width:738px;font-size:11px;line-height:18.8px;font-weight:300;color:var(--ink)}

.section-title{position:absolute;font-size:22px;color:var(--red)}
.article{position:absolute;top:674px;width:240px}
.article time{display:block;font-size:14px;font-weight:300;color:#555;margin-bottom:10px}
.article h3{font-size:11.2px;line-height:18.8px;font-weight:700;color:var(--red)}
.article p{font-size:11.2px;line-height:18.8px;font-weight:300;color:var(--ink)}
.article.faded p{color:var(--muted)}

.gallery-item{position:absolute;width:158px}
.gallery-item .photo{height:94px}
.gallery-item figcaption{font-size:9px;color:var(--muted);font-weight:300;margin-top:5px;margin-left:-2px}

.calendar{position:absolute;left:605px;top:863px;width:235px;background:var(--white)}
.cal-head{height:36px;background:var(--cal-head);display:flex;align-items:center;justify-content:space-between;padding:0 10px}
.cal-head .month{font-family:"Bebas Neue",sans-serif;font-size:22px;color:var(--white)}
.cal-days{display:grid;grid-template-columns:repeat(7,1fr);background:var(--page);font-size:7.5px;font-weight:600;color:#555;text-align:center;height:24px;line-height:24px}
.cal-grid{display:grid;grid-template-columns:repeat(7,1fr);grid-auto-rows:33.3px;border-left:1px solid var(--line);border-top:1px solid var(--line)}
.cal-grid span{position:relative;border-right:1px solid var(--line);border-bottom:1px solid var(--line);display:flex;align-items:center;justify-content:center;font-size:9.5px;font-weight:600;color:#333}
.cal-grid .out{color:#aaa;font-weight:400}
.cal-grid .today{background:var(--red);color:var(--white)}
.cal-grid .event::after{content:"";position:absolute;left:50%;top:24px;width:2px;height:2px;margin-left:-1px;border-radius:50%;background:currentColor}

.site-footer{position:absolute;left:0;top:1123px;width:942px;height:77px;background:var(--red);color:var(--white);text-align:center}
.footer-nav{padding-top:18px;font-size:11px}
.footer-nav a{color:var(--white);text-decoration:none}
.footer-nav .sep{margin:0 10px}
.copyright{font-size:11px;margin-top:8px}
</style>
</head>
<body>

<header>
  <div class="brand"><span class="brand-dot"></span><span class="brand-name">Vantage Fitness</span></div>
  <div class="search">Search</div>
  <nav class="main-nav">
    <a href="#">Latest News</a><a href="#">About Us</a><a href="#">Team</a><a href="#">Gallery</a><a href="#">Membership</a><a href="#">Classes</a><a href="#">Member Log In</a><a href="#">Contact Us</a><a href="#">Location</a>
  </nav>
</header>

<section class="hero">
  <div class="hero-photo" role="img" aria-label="Two athletes lifting dumbbells against a red backdrop"></div>
  <h2 class="hero-title display"><span class="l1">Our Space Is The</span><span class="l2">Biggest In The Country</span></h2>
  <svg class="hero-arrows" width="38" height="22" viewBox="0 0 38 22">
    <polyline points="12,2 3,11 12,20" fill="none" stroke="#c4121c" stroke-width="3"/>
    <polyline points="26,2 35,11 26,20" fill="none" stroke="#c4121c" stroke-width="3"/>
  </svg>
</section>

<aside class="social">
  <a href="#">kinwall</a>
  <a href="#">chirplo</a>
  <a href="#">snapvault</a>
</aside>

<section class="welcome">
  <h1 class="display">Welcome to Vantage Fitness</h1>
  <p>Lorem Ipsum is simply dummy text of the printing and typesetting industry. Lorem Ipsum has been the industry's standard dummy text ever since the 1500s, when an unknown printer took a galley of type and scrambled it to make a type specimen book. It has survived not only five centuries, but also the leap into electronic typesetting, remaining essentially unchanged. It was popularised in the 1960s with the release of Inkfield sheets containing Lorem Ipsum passages, and more recently with desktop publishing software like Quillset Layout including versions of Lorem Ipsum.</p>
</section>

<h2 class="section-title display" style="left:102px;top:638px">Latest Article</h2>
<article class="article" style="left:102px">
  <time>12-2-2014</time>
  <h3>Lorem Ipsum is simply dummy text of the printing and typesetting industry.</h3>
  <p>Lorem Ipsum has been the industry's standard dummy text ever since the 1500s, when an unknown printer took</p>
</article>
<article class="article" style="left:354px">
  <time>12-2-2014</time>
  <h3>Lorem Ipsum is simply dummy text of the printing and typesetting industry.</h3>
  <p>Lorem Ipsum has been the industry's standard dummy text ever since the 1500s, when an unknown printer took</p>
</article>
<article class="article faded" style="left:606px">
  <time>12-2-2014</time>
  <h3>Lorem Ipsum is simply dummy text of the printing and typesetting industry.</h3>
  <p>Lorem Ipsum has been the industry's standard dummy text ever since the 1500s, when an unknown printer took</p>
</article>

<h2 class="section-title display" style="left:102px;top:822px">Gallery</h2>
<figure class="gallery-item" style="left:102px;top:863px"><div class="photo" role="img" aria-label="Athlete curling a dumbbell" style="background:linear-gradient(90deg,#f4f4f4,#d9a07a 45%,#3a3a3a)"></div><figcaption>Neque porro quisquam est qui</figcaption></figure>
<figure class="gallery-item" style="left:265px;top:863px"><div class="photo" role="img" aria-label="Two women training with weights" style="background:linear-gradient(90deg,#b3262a,#d8a08a 50%,#e0a040)"></div><figcaption>Neque porro quisquam est qui</figcaption></figure>
<figure class="gallery-item" style="left:429px;top:863px"><div class="photo" role="img" aria-label="Athlete raising a dumbbell sideways" style="background:linear-gradient(90deg,#2a2d38,#5a3a2e 55%,#22252e)"></div><figcaption>Neque porro quisquam est qui</figcaption></figure>
<figure class="gallery-item" style="left:102px;top:981px"><div class="photo" role="img" aria-label="Athlete training on a cable machine" style="background:linear-gradient(90deg,#7a7a7a,#c69070 50%,#5a5a5a)"></div><figcaption>Neque porro quisquam est qui</figcaption></figure>
<figure class="gallery-item" style="left:265px;top:981px"><div class="photo" role="img" aria-label="Trainer coaching a woman with a dumbbell" style="background:linear-gradient(90deg,#8a8a8a,#c9b0a0 50%,#f2f2f2)"></div><figcaption>Neque porro quisquam est qui</figcaption></figure>
<figure class="gallery-item" style="left:429px;top:981px"><div class="photo" role="img" aria-label="Fit couple posing in black and white" style="background:linear-gradient(90deg,#111,#6a6a6a 50%,#151515)"></div><figcaption>Neque porro quisquam est qui</figcaption></figure>

<h2 class="section-title display" style="left:602px;top:822px">Calendar Activity</h2>
<section class="calendar">
  <div class="cal-head">
    <svg width="10" height="12" viewBox="0 0 10 12"><polyline points="7,1 2,6 7,11" fill="none" stroke="#777" stroke-width="2"/></svg>
    <span class="month">January 2014</span>
    <svg width="10" height="12" viewBox="0 0 10 12"><polyline points="3,1 8,6 3,11" fill="none" stroke="#fff" stroke-width="2"/></svg>
  </div>
  <div class="cal-days"><span>MON</span><span>TUE</span><span>WED</span><span>THU</span><span>FRI</span><span>SAT</span><span>SUN</span></div>
  <div class="cal-grid">
    <span class="out event">30</span><span>1</span><span class="event">2</span><span>3</span><span>4</span><span>5</span><span>6</span>
    <span>7</span><span>8</span><span>9</span><span>10</span><span>11</span><span class="today event">12</span><span>13</span>
    <span>14</span><span>15</span><span class="event">16</span><span class="event">17</span><span>18</span><span>19</span><span>20</span>
    <span class="event">21</span><span>22</span><span>23</span><span>24</span><span>25</span><span>26</span><span>27</span>
    <span>28</span><span>29</span><span>30</span><span>31</span><span class="out">1</span><span class="out">2</span><span class="out">3</span>
  </div>
</section>

<footer class="site-footer">
  <nav class="footer-nav">
    <a href="#">Latest News</a><span class="sep">|</span><a href="#">About us</a><span class="sep">|</span><a href="#">Team</a><span class="sep">|</span><a href="#">Gallery</a><span class="sep">|</span><a href="#">Membership</a><span class="sep">|</span><a href="#">Classes</a><span class="sep">|</span><a href="#">Member Log In</a><span class="sep">|</span><a href="#">Contact Us</a><span class="sep">|</span><a href="#">Location</a>
  </nav>
  <p class="copyright">© Copyrights Company Name, All Rights Reserved</p>
</footer>

</body>
</html>
```